Quorimo Business Card Design Project

We need a business card design for quorimo.example a company based in Berlin, Germany.

?Quorimo is marketplace that enables people all over the world to monetize and exchange their individual knowledge and language skills through interactive video sessions. User are matched by their interests.

On Quorimo everybody can be student or teacher (seller or buyer).

We would love to see designs that use or main color blue and green. The design should communicate what Quorimo enables - see my notice above.

Looking so forward to your designs
Cheers from Berlin,
Lorenz

Target Market(s)

globally

Industry/Entity Type

Teacher

Requirements
Must have
• Lorenz Hubeck
CEO
Quorimo.example

Quorimo e-Services GmbH
Lindenweg 87
10247 Berlin

Fon: +49 30 418 906 25 17
Mobile: 49 172 54 91 37 6
E-Mail: l.hubeck@quorimo.example
Web: www.quorimo.example

```html
<!DOCTYPE html>
<html lang="en">
<head>
<meta charset="utf-8">
<title>Quorimo Business Card</title>
<link rel="stylesheet" href="https://fonts.googleapis.com/css2?family=Exo+2:wght@400;500;600&display=swap">
<style>
  :root {
    --bg: #000000;
    --card: #ffffff;
    --blue: #0597c9;
    --blue-text: #1a9fd4;
    --green: #9cc01c;
    --grey: #6a6a6a;
    --grey-dark: #4d4d4d;
    --ink: #222222;
    --rule: #cfcfcf;
  }
  * { box-sizing: border-box; margin: 0; padding: 0; }
  html, body { width: 1200px; height: 405px; overflow: hidden; background: var(--bg); }
  body { position: relative; font-family: "Exo 2", sans-serif; }

  .card {
    position: absolute;
    width: 526px; height: 300px;
    background: var(--card);
    border-radius: 14px;
    overflow: hidden;
  }
  .card--front { left: 44px; top: 50px; }
  .card--back  { left: 622px; top: 48px; }

  .card__waves { position: absolute; inset: 0; width: 100%; height: 100%; }

  .brand { position: absolute; display: flex; align-items: center; }
  .brand__mark { flex: none; background: var(--green); border-radius: 3px; }
  .brand__name {
    color: var(--grey);
    font-weight: 500;
    line-height: 1;
    letter-spacing: 0.5px;
  }

  .card--front .brand { left: 22px; top: 84px; height: 54px; }
  .card--front .brand__mark { width: 46px; height: 46px; margin-right: 14px; }
  .card--front .brand__name { font-size: 54px; }

  .card--back .brand { left: 92px; top: 98px; height: 70px; }
  .card--back .brand__mark { width: 60px; height: 60px; margin-right: 18px; }
  .card--back .brand__name { font-size: 70px; }

  .divider {
    position: absolute;
    left: 326px; top: 40px;
    width: 1px; height: 168px;
    background: var(--rule);
  }

  .contact { position: absolute; left: 337px; top: 38px; color: var(--grey-dark); }
  .contact__name { color: var(--blue-text); font-weight: 600; font-size: 16px; }
  .contact__role { font-size: 13px; margin-top: 3px; }
  .contact__list { list-style: none; margin-top: 24px; }
  .contact__item {
    display: flex; align-items: center;
    font-size: 13px; height: 18.5px;
  }
  .contact__item svg { width: 11px; height: 11px; margin-right: 9px; fill: var(--grey-dark); flex: none; }
  .contact__address { font-size: 13px; margin-top: 13px; line-height: 17px; margin-left: -4px; }

  .back__web {
    position: absolute; left: 24px; top: 269px;
    color: var(--ink); font-size: 11.5px; font-weight: 500; letter-spacing: 0.6px;
  }
</style>
</head>
<body>

<svg width="0" height="0" style="position:absolute" aria-hidden="true">
  <defs>
    <linearGradient id="silver" x1="0" y1="0" x2="1" y2="0">
      <stop offset="0" stop-color="#8a8a8a"/>
      <stop offset="0.3" stop-color="#f2f2f2"/>
      <stop offset="0.6" stop-color="#9a9a9a"/>
      <stop offset="1" stop-color="#d8d8d8"/>
    </linearGradient>
    <symbol id="waves" viewBox="0 0 526 300" preserveAspectRatio="none">
      <path d="M0,160 C100,236 230,278 330,283 L330,286 C210,284 90,250 0,196 Z" fill="var(--green)"/>
      <path d="M0,180 C100,250 230,282 330,285 L330,288 C200,288 80,254 0,205 Z" fill="url(#silver)"/>
      <path d="M0,200 C120,275 300,305 526,247 L526,300 L0,300 Z" fill="var(--blue)"/>
    </symbol>
  </defs>
</svg>

<section class="card card--front">
  <svg class="card__waves" aria-hidden="true"><use href="#waves"/></svg>

  <div class="brand">
    <span class="brand__mark"></span>
    <span class="brand__name">Quorimo</span>
  </div>

  <div class="divider"></div>

  <div class="contact">
    <p class="contact__name">Lorenz Hubeck,</p>
    <p class="contact__role">CEO</p>
    <ul class="contact__list">
      <li class="contact__item">
        <svg viewBox="0 0 12 12"><path d="M2.5 0.5 L4.5 0.5 L5.2 3.2 L3.8 4.3 C4.5 5.8 5.9 7.3 7.6 8.1 L8.7 6.8 L11.5 7.5 L11.5 9.6 C11.5 10.8 10.6 11.5 9.5 11.4 C4.8 10.9 1.1 7.2 0.6 2.5 C0.5 1.4 1.3 0.5 2.5 0.5 Z"/></svg>
        +49 30 418 906 25 17
      </li>
      <li class="contact__item">
        <svg viewBox="0 0 12 12"><path d="M3 0 H9 V12 H3 Z M4 1.5 V7 H8 V1.5 Z M4.3 8.2 h1 v1 h-1 z M5.5 8.2 h1 v1 h-1 z M6.7 8.2 h1 v1 h-1 z M4.3 9.8 h1 v1 h-1 z M5.5 9.8 h1 v1 h-1 z M6.7 9.8 h1 v1 h-1 z"/></svg>
        49 172 54 91 37 6
      </li>
      <li class="contact__item">
        <svg viewBox="0 0 12 12"><path d="M6 1 L12 5 V11 H0 V5 Z M1 5.6 L6 8.6 L11 5.6 L6 2.2 Z"/></svg>
        l.hubeck@quorimo.example
      </li>
      <li class="contact__item">
        <svg viewBox="0 0 12 12"><path d="M6 0.5 A5.5 5.5 0 1 1 5.99 0.5 Z M1.6 4 H10.4 V5 H1.6 Z M1.2 7 H10.8 V8 H1.2 Z"/></svg>
        www.quorimo.example
      </li>
    </ul>
    <p class="contact__address">Quorimo e-Services GmbH<br>Lindenweg 87 10247 Berlin</p>
  </div>
</section>

<section class="card card--back">
  <svg class="card__waves" aria-hidden="true"><use href="#waves"/></svg>

  <div class="brand">
    <span class="brand__mark"></span>
    <span class="brand__name">Quorimo</span>
  </div>

  <p class="back__web">www.quorimo.example</p>
</section>

</body>
</html>
```